Business Card Design for Occupational Medicine Start Up Company

We need to design a professional business card. We are a healthcare company providing occupational medicine services to blue collar industries. We are professional, efficient and high quality service providers.

Target Market(s)

Blue Collar Industry: Shipbuilding, Ports, Trucking Companies; The Executives and Safety Officers for these companies

Industry/Entity Type

Healthcare

Contact Information for Business Card

Logo, Name, Title, Email, Phone

Other font styles liked:
• Please match our Brand Guide

Requirements
Must have
• Our Company Colors and Logo

```html
<!DOCTYPE html>
<html lang="en">
<head>
<meta charset="utf-8">
<title>Crewline Clinics – Business Card</title>
<link rel="stylesheet" href="https://fonts.googleapis.com/css2?family=Montserrat:wght@400;700&display=swap">
<style>
  :root {
    --page-bg: #c9c9c9;
    --card-bg: #1a1a1a;
    --ink: #ffffff;
    --mark-grey: #8a8a8a;
  }
  * { box-sizing: border-box; margin: 0; padding: 0; }
  html, body {
    width: 1200px; height: 846px; overflow: hidden;
    background: var(--page-bg);
    font-family: "Montserrat", sans-serif;
    color: var(--ink);
  }
  .card {
    position: absolute;
    left: 348px;
    width: 507px; height: 290px;
    border-radius: 31px;
    background: var(--card-bg);
  }
  .card--front { top: 114px; }
  .card--back { top: 443px; }

  .brand {
    position: absolute;
    display: flex; flex-direction: column; align-items: center;
    font-weight: 700;
    text-transform: uppercase;
    text-align: center;
  }
  .brand__dot {
    border-radius: 50%;
    background: var(--mark-grey);
  }
  .card--front .brand { left: 57px; top: 102px; width: 140px; }
  .card--front .brand__dot { width: 38px; height: 38px; margin-bottom: 10px; }
  .card--front .brand__name { font-size: 15px; letter-spacing: 0.5px; line-height: 1.15; }

  .card--back .brand { left: 0; top: 60px; width: 100%; }
  .card--back .brand__dot { width: 70px; height: 70px; margin-bottom: 18px; }
  .card--back .brand__name { font-size: 30px; letter-spacing: 0.5px; line-height: 1; }
  .card--back .brand__sub { font-size: 17px; letter-spacing: 7px; margin-top: 6px; padding-left: 7px; }

  .person { position: absolute; left: 245px; top: 92px; }
  .person__name { font-size: 18px; font-weight: 700; letter-spacing: 0.3px; line-height: 1.05; }
  .person__title { font-size: 13px; font-weight: 700; line-height: 1.3; }

  .contacts { position: absolute; left: 214px; top: 160px; list-style: none; }
  .contacts__item {
    display: flex; align-items: center;
    height: 24.5px;
    font-size: 14px; font-weight: 400; letter-spacing: 0.2px;
  }
  .contacts__icon { width: 21px; height: 18px; margin-right: 10px; flex: none; }
</style>
</head>
<body>
  <section class="card card--front" aria-label="Card front">
    <div class="brand">
      <span class="brand__dot"></span>
      <span class="brand__name">Crewline<br>Clinics</span>
    </div>
    <div class="person">
      <p class="person__name">FULL NAME</p>
      <p class="person__title">Title</p>
    </div>
    <ul class="contacts">
      <li class="contacts__item">
        <svg class="contacts__icon" viewBox="0 0 24 24" aria-hidden="true"><path fill="#fff" d="M6.6 2.5l2.6 4.2-1.8 1.7c.9 3 2.8 5.6 5.4 7.4l1.9-1.5 4 2.8-1.6 3.4c-6.4-.6-12.7-7.8-12.6-15z"/></svg>
        <span>123-456-7890</span>
      </li>
      <li class="contacts__item">
        <svg class="contacts__icon" viewBox="0 0 24 18" aria-hidden="true"><rect x="1" y="1" width="22" height="16" fill="#fff"/><path d="M1.5 1.5L12 10l10.5-8.5M1.5 16.5l8-7M22.5 16.5l-8-7" stroke="#1a1a1a" stroke-width="1.6" fill="none"/></svg>
        <span>full.name@crewlineclinics.com</span>
      </li>
      <li class="contacts__item">
        <svg class="contacts__icon" viewBox="0 0 24 24" aria-hidden="true"><circle cx="12" cy="12" r="11" fill="#fff"/><g stroke="#1a1a1a" stroke-width="1" fill="none"><ellipse cx="12" cy="12" rx="4.5" ry="11"/><path d="M12 1v22M1 12h22M3 6.5h18M3 17.5h18"/></g></svg>
        <span>CREWLINECLINICS.COM</span>
      </li>
    </ul>
  </section>

  <section class="card card--back" aria-label="Card back">
    <div class="brand">
      <span class="brand__dot"></span>
      <span class="brand__name">Crewline</span>
      <span class="brand__name brand__sub">Clinics</span>
    </div>
  </section>
</body>
</html>
```